Meridale Partners Website

Meridale Partners (MP) provide Analytics & Enterprise Performance Management (EPM) advisory & consultancy services. We are passionate about data and making a difference for our clients by working in partnership with them, helping them on their journey to becoming an Meridale Partner. We deliver insights which give our clients a competitive edge and a much deeper understanding of their organisation.

We need a website which shows who we are, what we do and how we do it.

www.meridale-partners.example is our very basic website at the moment. We want to completely revamp it with a corporate look

```html
<!DOCTYPE html>
<html lang="en">
<head>
<meta charset="utf-8">
<title>Meridale Partners</title>
<link rel="stylesheet" href="https://fonts.googleapis.com/css2?family=Poppins:wght@300;400;500;600&display=swap">
<style>
:root{
  --navy:#2d5570;
  --navy-deep:#24465e;
  --coral:#fe7a5d;
  --mist:#f4f6f8;
  --white:#ffffff;
  --copy:#6f6f6f;
}
*{margin:0;padding:0;box-sizing:border-box}
html,body{width:1200px;height:3919px;overflow:hidden}
body{position:relative;background:var(--mist);font-family:"Poppins",sans-serif;color:var(--navy)}
.abs{position:absolute}
.layer{position:absolute;left:0;top:0}
.brand{display:flex;align-items:center;gap:12px}
.brand-dot{width:44px;height:44px;border-radius:50%;background:var(--navy)}
.brand-name{font-weight:600;font-size:19px;line-height:21px;letter-spacing:.5px;color:var(--navy)}
.nav{left:660px;top:31px}
.nav a{position:absolute;white-space:nowrap;color:var(--white);font-weight:500;font-size:13.5px;text-decoration:none}
.hero-title{left:59px;top:160px;font-weight:500;font-size:82px;line-height:98px;color:var(--navy);letter-spacing:-.5px}
.hero-sub{left:61px;top:364px;font-size:22px;font-weight:400;color:#3c4a55}
.pill{display:flex;align-items:center;justify-content:center;border-radius:24px;font-weight:500;font-size:14.5px}
.pill-navy{background:var(--navy);color:var(--white)}
.section-title{left:0;width:1200px;text-align:center;font-weight:600;font-size:39px;letter-spacing:-.5px;color:var(--navy)}
.who-title{left:660px;top:712px;font-weight:600;font-size:39px;letter-spacing:-.5px}
.who-sub{left:668px;top:766px;font-size:17px;font-weight:400}
.who-copy{left:668px;top:826px;width:400px;font-size:13.3px;line-height:26.5px;font-weight:300;color:var(--copy)}
.service{width:336px;text-align:center}
.service h3{font-weight:500;font-size:16px;color:var(--navy);margin-top:8px}
.service p{font-size:13.5px;font-weight:300;line-height:26px;color:var(--copy);margin-top:16px;padding:0 12px}
.service-card{left:432px;top:1282px;width:336px;height:283px;background:var(--white)}
.step-label{font-weight:600;font-size:14.5px;color:var(--navy);white-space:nowrap}
.quote-title{left:0;top:2525px;width:1200px;text-align:center;font-weight:600;font-size:39px;color:var(--white);letter-spacing:-.5px}
.quote-copy{left:270px;top:2597px;width:660px;text-align:center;font-size:14px;line-height:26.5px;font-weight:300;color:var(--white)}
.client-name{left:0;top:2816px;width:1200px;text-align:center;font-size:14px;font-weight:500;color:var(--white)}
.cta-card{left:224px;top:3124px;width:752px;height:313px;background:var(--navy)}
.cta-accent{left:640px;top:3124px;width:336px;height:313px;background:var(--coral)}
.cta-photo{left:582px;top:3092px;width:118px;height:404px;border-radius:6px;background:linear-gradient(180deg,#9aa3a9,#6e767b)}
.cta-title{left:256px;top:3150px;font-size:30px;line-height:37px;font-weight:500;color:var(--white)}
.cta-copy{left:256px;top:3229px;width:300px;font-size:11.5px;line-height:22px;font-weight:300;color:var(--white)}
.cta-btn{left:254px;top:3304px;width:146px;height:46px;background:var(--white);color:var(--navy);border-radius:4px;font-size:14px}
.partner{left:262px;top:3378px;display:flex;align-items:center;gap:10px;color:var(--white)}
.partner b{font-weight:500;font-size:13px;letter-spacing:1px}
.partner i{display:block;width:1px;height:30px;background:var(--white)}
.partner span{font-size:12px;font-weight:300}
.cta-side{left:720px;top:3188px;width:220px;text-align:right;font-size:12.5px;line-height:22.5px;font-weight:300;color:var(--white)}
.cta-phone{left:700px;top:3298px;width:240px;text-align:right;font-size:33px;font-weight:500;color:var(--white)}
.cta-call{left:700px;top:3346px;width:236px;text-align:right;font-size:16px;font-weight:400;color:var(--white)}
.foot-copy{left:61px;top:3787px;font-size:12px;font-weight:300;color:var(--white)}
.social{width:36px;height:36px;border-radius:50%;background:var(--white)}
.foot-links a{position:absolute;left:433px;font-size:12.5px;font-weight:300;color:var(--white);text-decoration:none;white-space:nowrap}
.foot-info{position:absolute;left:834px;font-size:12px;line-height:23px;font-weight:300;color:var(--white)}
</style>
</head>
<body>

<!-- background shapes -->
<svg class="layer" width="1200" height="3919" viewBox="0 0 1200 3919" aria-hidden="true">
  <defs>
    <linearGradient id="heroPhoto" x1="0" y1="0" x2="1" y2="1">
      <stop offset="0" stop-color="#3b5366"/>
      <stop offset=".5" stop-color="#5b7186"/>
      <stop offset="1" stop-color="#2b3d4e"/>
    </linearGradient>
    <linearGradient id="cityPhoto" x1="0" y1="0" x2="0" y2="1">
      <stop offset="0" stop-color="#4b7189"/>
      <stop offset="1" stop-color="#2d5570"/>
    </linearGradient>
  </defs>
  <path fill="#ffffff" d="M0,680 C260,580 620,610 900,600 C1020,596 1120,585 1200,575 L1200,1180 C1000,1110 820,1115 600,1100 C380,1085 220,1070 0,985 Z"/>
  <path fill="#ffffff" d="M0,1735 C160,1680 300,1690 520,1720 C760,1755 1000,1780 1200,1905 L1200,2400 L0,2400 Z"/>
  <path fill="url(#cityPhoto)" d="M0,2397 L1200,2397 L1200,2935 C1000,2990 820,3015 640,3018 C420,3022 180,3010 0,3068 Z" role="img" aria-label="City skyline photograph behind client testimonials"/>
  <path fill="var(--navy)" d="M0,3512 C180,3510 360,3545 560,3590 C780,3640 1000,3660 1200,3670 L1200,3919 L0,3919 Z"/>
  <path fill="var(--navy)" d="M584,0 C572,150 600,330 700,455 C790,560 960,545 1100,565 C1150,575 1190,592 1200,600 L1200,0 Z"/>
  <path fill="url(#heroPhoto)" d="M612,0 C598,130 640,280 762,362 C870,432 1010,445 1200,590 L1200,0 Z" role="img" aria-label="Photo of a consultant explaining a growth report in a meeting"/>
</svg>

<!-- header -->
<div class="abs brand" style="left:61px;top:14px">
  <div class="brand-dot"></div>
  <div class="brand-name">MERIDALE<br>PARTNERS</div>
</div>
<nav class="abs nav">
  <a style="left:0">Home</a>
  <a style="left:72px">Who We Are</a>
  <a style="left:184px">What We Do</a>
  <a style="left:298px">How We Do</a>
  <a style="left:405px">Contact Us</a>
</nav>

<h1 class="abs hero-title">Meridale<br>Partners</h1>
<p class="abs hero-sub">DATA ANALYTICS &amp; EPM Consulting Services</p>
<div class="abs pill pill-navy" style="left:61px;top:414px;width:144px;height:42px">Contact Us</div>

<!-- who we are -->
<svg class="abs" style="left:100px;top:627px" width="490" height="490" viewBox="0 0 490 490" role="img" aria-label="Illustration of a team meeting around a table, seen from above">
  <defs>
    <radialGradient id="meetingTone" cx=".5" cy=".45" r=".55">
      <stop offset="0" stop-color="#dfe7ec"/>
      <stop offset="1" stop-color="#eef2f4"/>
    </radialGradient>
  </defs>
  <circle cx="245" cy="245" r="239" fill="url(#meetingTone)"/>
</svg>
<h2 class="abs who-title">WHO WE ARE</h2>
<p class="abs who-sub">Meridale Partners</p>
<p class="abs who-copy">MP are a Data Analytics &amp; EPM company, specialising in the implementation and support of Business Intelligence, EPM and Data Analytics business solutions, both in the Cloud and on-premise.</p>
<div class="abs pill pill-navy" style="left:666px;top:963px;width:145px;height:43px;font-size:13.5px">READ MORE</div>

<!-- what we do -->
<h2 class="abs section-title" style="top:1202px">WHAT WE DO</h2>
<div class="abs service-card"></div>

<svg width="0" height="0" style="position:absolute">
  <defs>
    <g id="blob">
      <ellipse cx="45" cy="46" rx="40" ry="33" fill="var(--navy)" transform="rotate(-40 45 46)"/>
      <circle cx="45" cy="43" r="33" fill="#ffffff"/>
      <circle cx="45" cy="43" r="33" fill="none" stroke="#e8ecef"/>
    </g>
  </defs>
</svg>

<div class="abs service" style="left:57px;top:1310px">
  <svg width="90" height="90" viewBox="0 0 90 90" aria-hidden="true"><use href="#blob"/>
    <g fill="none" stroke="var(--navy)" stroke-width="1.6"><circle cx="35" cy="36" r="4"/><circle cx="45" cy="34" r="4"/><circle cx="55" cy="36" r="4"/><path d="M28 55v-8a7 7 0 0 1 14 0M38 55v-10a7 7 0 0 1 14 0M48 55v-8a7 7 0 0 1 14 0"/></g></svg>
  <h3>Advise &amp; Architect</h3>
  <p>Helping our customers understand the art of the possible and safeguarding their investments by overseeing implementations.</p>
</div>
<div class="abs service" style="left:432px;top:1310px">
  <svg width="90" height="90" viewBox="0 0 90 90" aria-hidden="true"><use href="#blob"/>
    <g fill="none" stroke="var(--navy)" stroke-width="1.6"><path d="M45 30a10 10 0 0 0-6 18v5h12v-5a10 10 0 0 0-6-18z"/><path d="M40 57h10M45 22v3M33 27l2 2M57 27l-2 2"/></g></svg>
  <h3>Design &amp; Implement</h3>
  <p>Working with the project management team, through each stage of the project, with clearly defined deliverables and well exercised...</p>
</div>
<div class="abs service" style="left:802px;top:1310px">
  <svg width="90" height="90" viewBox="0 0 90 90" aria-hidden="true"><use href="#blob"/>
    <g fill="none" stroke="var(--navy)" stroke-width="1.6"><circle cx="45" cy="43" r="5"/><circle cx="45" cy="43" r="11" stroke-dasharray="5 3"/><circle cx="45" cy="43" r="15"/></g></svg>
  <h3>Optimise &amp; Manage</h3>
  <p>Our Managed Services delivers proactive, on-demand support for EPM and Data Analytics environments...</p>
</div>

<!-- how we do -->
<h2 class="abs section-title" style="top:1831px">HOW WE DO</h2>
<svg class="layer" width="1200" height="2400" viewBox="0 0 1200 2400" aria-hidden="true">
  <g fill="none" stroke="var(--navy)" stroke-width="2.2">
    <path d="M476 2011 A128 124 0 0 0 730 2011"/>
    <line x1="446" y1="2016" x2="476" y2="2011"/>
    <line x1="499" y1="2084" x2="466" y2="2120"/>
    <line x1="604" y1="2134" x2="604" y2="2180"/>
    <line x1="695" y1="2088" x2="724" y2="2120"/>
    <line x1="730" y1="2011" x2="758" y2="2016"/>
  </g>
  <g fill="#ffffff" stroke="var(--navy)" stroke-width="2.2">
    <circle cx="476" cy="2011" r="6"/><circle cx="499" cy="2084" r="6"/><circle cx="604" cy="2134" r="6"/><circle cx="695" cy="2088" r="6"/><circle cx="730" cy="2011" r="6"/>
  </g>
  <circle cx="604" cy="2010" r="96" fill="#ffffff" stroke="#eceff2" stroke-width="2"/>
  <path fill="var(--navy)" d="M570 2186 C600 2170 650 2180 665 2215 C680 2250 660 2290 618 2292 C580 2294 548 2270 550 2240 C552 2210 548 2198 570 2186 Z"/>
</svg>
<div class="abs brand" style="left:528px;top:1992px;gap:8px">
  <div class="brand-dot" style="width:30px;height:30px"></div>
  <div class="brand-name" style="font-size:13px;line-height:15px">MERIDALE<br>PARTNERS</div>
</div>
<div class="abs" style="left:555px;top:2207px;width:100px;text-align:center;color:#fff;font-size:19px;line-height:26px;font-weight:500">Contact<br>Us</div>

<svg class="abs" style="left:354px;top:1972px" width="90" height="90" viewBox="0 0 90 90" aria-hidden="true"><use href="#blob"/>
  <g fill="none" stroke="var(--navy)" stroke-width="1.6"><rect x="29" y="32" width="20" height="14" rx="3"/><rect x="41" y="38" width="20" height="14" rx="3"/></g></svg>
<svg class="abs" style="left:399px;top:2090px" width="90" height="90" viewBox="0 0 90 90" aria-hidden="true"><use href="#blob"/>
  <g fill="none" stroke="var(--navy)" stroke-width="1.6"><rect x="33" y="31" width="12" height="12"/><rect x="45" y="43" width="12" height="12"/><circle cx="51" cy="37" r="3"/></g></svg>
<svg class="abs" style="left:751px;top:1972px" width="90" height="90" viewBox="0 0 90 90" aria-hidden="true"><use href="#blob"/>
  <g fill="none" stroke="var(--navy)" stroke-width="1.6"><path d="M30 56h30M34 56v-8h5v8M42 56v-12h5v12M50 56v-17h5v17M32 40l8-7 5 4 10-9"/></g></svg>
<svg class="abs" style="left:703px;top:2096px" width="90" height="90" viewBox="0 0 90 90" aria-hidden="true"><use href="#blob"/>
  <g fill="none" stroke="var(--navy)" stroke-width="1.6"><path d="M30 34h30M30 44h30M30 54h30"/><circle cx="38" cy="34" r="3"/><circle cx="52" cy="44" r="3"/><circle cx="42" cy="54" r="3"/></g></svg>

<div class="abs step-label" style="right:858px;top:2007px">Conversation</div>
<div class="abs step-label" style="right:812px;top:2126px">Design &amp; Planning</div>
<div class="abs step-label" style="left:849px;top:2009px">Grow your Business</div>
<div class="abs step-label" style="left:800px;top:2134px">Improvement</div>

<!-- testimonials -->
<svg class="layer" width="1200" height="2900" viewBox="0 0 1200 2900" aria-hidden="true">
  <circle cx="599" cy="2494" r="21" fill="#ffffff"/>
  <path fill="var(--navy)" d="M586 2490a5 5 0 0 1 5-5v3a3 3 0 0 0-2 3h3v7h-6zM599 2490a5 5 0 0 1 5-5v3a3 3 0 0 0-2 3h3v7h-6z"/>
  <circle cx="578" cy="2866" r="3.5" fill="#ffffff"/>
  <circle cx="600" cy="2866" r="7" fill="none" stroke="#ffffff" stroke-width="1.5"/>
  <circle cx="600" cy="2866" r="3.5" fill="#ffffff"/>
  <circle cx="622" cy="2866" r="3.5" fill="#ffffff"/>
</svg>
<svg class="layer" width="1200" height="2900" viewBox="0 0 1200 2900" role="img" aria-label="Client portrait photographs">
  <g stroke="#ffffff" stroke-width="3">
    <circle cx="599" cy="2747" r="53" fill="#c9b7a8"/>
    <circle cx="274" cy="2543" r="37" fill="#d8b89c"/>
    <circle cx="925" cy="2560" r="29" fill="#b9a89a"/>
    <circle cx="228" cy="2666" r="26" fill="#a99383"/>
    <circle cx="980" cy="2671" r="37" fill="#c1b0a2"/>
    <circle cx="403" cy="2815" r="29" fill="#d6b395"/>
    <circle cx="896" cy="2799" r="29" fill="#d9a98a"/>
  </g>
</svg>
<h2 class="abs quote-title">WHAT OUR CLIENTS SAY</h2>
<p class="abs quote-copy">Lorem Ipsum is simply dummy text of the printing and typesetting industry. Lorem Ipsum has been the industry's standard dummy text ever since the 1500s, when an unknown printer took a galley of type and scrambled it to make a type specimen book.</p>
<p class="abs client-name">- Client Name</p>

<!-- call to action -->
<div class="abs cta-card"></div>
<div class="abs cta-accent"></div>
<div class="abs cta-photo" role="img" aria-label="Photo of a smiling consultant standing in a grey suit"></div>
<h2 class="abs cta-title">Contact Us to Discuss<br>Your Business Needs</h2>
<p class="abs cta-copy">Lorem Ipsum is simply dummy text of the printing and typesetting industry. Lorem Ipsum has been the industry.</p>
<div class="abs pill cta-btn">CONTACT US</div>
<div class="abs partner"><b>CORVANE</b><i></i><span>Partner</span></div>
<p class="abs cta-side">Lorem Ipsum is simply dummy text of the printing and type setting industry. Lorem Ipsum has been the industry.</p>
<p class="abs cta-phone">01 480 2275</p>
<p class="abs cta-call">CALL US NOW</p>

<!-- footer -->
<div class="abs brand" style="left:61px;top:3700px">
  <div class="brand-dot" style="background:#fff"></div>
  <div class="brand-name" style="color:#fff">MERIDALE<br>PARTNERS</div>
</div>
<p class="abs foot-copy">© Meridale Partners - 2022. All Rights Reserved.</p>
<div class="abs social" style="left:60px;top:3830px" aria-label="Professional network profile"></div>
<div class="abs social" style="left:113px;top:3830px" aria-label="Social feed profile"></div>
<div class="foot-links">
  <a style="top:3705px">Home</a>
  <a style="top:3735px">Who we Are</a>
  <a style="top:3765px">What We Do</a>
  <a style="top:3795px">How We Do</a>
  <a style="top:3825px">Contact Us</a>
</div>
<svg class="layer" width="1200" height="3919" viewBox="0 0 1200 3919" aria-hidden="true">
  <g fill="#ffffff">
    <path d="M802 3716h14v10h-14z M802 3716l7 5 7-5" stroke="var(--navy)" stroke-width="1"/>
    <path d="M804 3774c1-2 3-2 4 0l1 2c0 1-1 2-1 2 1 2 3 4 5 5 0 0 1-1 2-1l2 1c2 1 2 3 0 4-4 3-15-8-13-13z"/>
    <path d="M811 3812a5 5 0 0 0-5 5c0 4 5 9 5 9s5-5 5-9a5 5 0 0 0-5-5z"/>
    <circle cx="811" cy="3817" r="1.8" fill="var(--navy)"/>
  </g>
</svg>
<p class="foot-info" style="top:3709px">14 Harbour View Road,<br>Ashgrove, Dublin 4, D04 KR21</p>
<p class="foot-info" style="top:3770px">01 480 2275</p>
<p class="foot-info" style="top:3812px">info@meridale-partners.example</p>

</body>
</html>
```